Brackenford Fluidworks needs a website describing the repair business we are in.

Brackenford Fluidworks is a full hydraulic repair facility. We have 2 shops. We repair and service all hydraulic cylinders, pneumatic cylinders, hydraulic pumps, motors, valves and gearboxes. Our services range from large industrial plants to the individual that owns one piece of equipment. We also offer removal and install of cylinders. Along with free pick up and delivery, within a certain distance which is usually 100 miles from one of our shops.

With over 30 years experience in the hydraulic business, we can repair or replace any job. There is not a job too big or too small, we service them all.

We have customers that send whole pieces of equipment to us to do complete overhauls on all the hydraulics. Ranging from a country club green roller to a 10 ton boom truck.

Target Market(s)

Industrial plants, road builders, dirt work companies, general contractors, owners of industrial equipment (bulldozers, excavators, loaders, scrapers, motor graders, etc.

Industry/Entity Type

Hydraulic

Number of Pages Required

5+ page

Font styles to use
Sans Serif

Colors
ec1f27
ffffff
aaaaaa

Requirements
Must have
• Information about what we offer and pictures of jobs completed.
Nice to have
• Nice stock photos of jobsites and industrial plants.
Should not have
• Any sort of comical characters.

```html
<!DOCTYPE html>
<html lang="en">
<head>
<meta charset="utf-8">
<title>Brackenford Fluidworks</title>
<link rel="stylesheet" href="https://fonts.googleapis.com/css2?family=Montserrat:wght@300;400;500;600;700&display=swap">
<style>
:root{
  --red:#ec1f27;
  --white:#ffffff;
  --grey:#aaaaaa;
  --ink:#111111;
  --text:#444444;
  --light:#f2f2f2;
  --ring:#1e1e1e;
}
*{margin:0;padding:0;box-sizing:border-box}
html,body{width:1200px;height:2177px;overflow:hidden}
body{position:relative;font-family:'Montserrat',sans-serif;background:var(--white);color:var(--ink)}
.abs{position:absolute}

/* hero */
.hero{left:0;top:0;width:1200px;height:570px;background:
  radial-gradient(ellipse 420px 160px at 250px 420px,rgba(214,150,90,.55),transparent 70%),
  radial-gradient(ellipse 500px 180px at 900px 380px,rgba(190,150,110,.45),transparent 70%),
  radial-gradient(ellipse 700px 120px at 600px 250px,rgba(120,130,150,.35),transparent 70%),
  linear-gradient(180deg,#1f2530 0%,#323a47 28%,#4a4b50 45%,#5e4c3e 62%,#3a302a 82%,#262220 100%)}
.hero-shade{left:0;top:0;width:1200px;height:570px;background:rgba(0,0,0,.18)}
.nav a{position:absolute;top:43px;height:33px;line-height:33px;color:var(--white);text-decoration:none;font-size:14.5px;font-weight:600;text-transform:uppercase}
.nav .active{background:var(--red);border-radius:17px;width:115px;text-align:center}
.brand-badge{left:500px;top:-56px;width:201px;height:201px;border-radius:50%;background:var(--white);display:flex;align-items:flex-end;justify-content:center;padding-bottom:48px;text-align:center}
.brand-name{color:var(--red);font-weight:700;font-size:17px;line-height:1.15;text-transform:uppercase}
.hero-title{left:0;top:246px;width:1200px;text-align:center;color:var(--white);font-size:53px;font-weight:600;line-height:64px}
.hero-sub{left:0;top:322px;width:1200px;text-align:center;color:var(--white);font-size:15.5px;font-weight:300}
.btn{display:block;background:var(--red);color:var(--white);text-align:center;text-transform:uppercase;font-weight:700;text-decoration:none;border-radius:30px}
.hero-btn{left:483px;top:371px;width:234px;height:55px;line-height:55px;font-size:15.5px}

/* services */
.welcome{left:0;top:570px;width:1200px;height:523px;background:
  radial-gradient(ellipse 300px 200px at 120px 330px,rgba(0,0,0,.06),transparent 70%),
  radial-gradient(ellipse 400px 220px at 1050px 330px,rgba(0,0,0,.05),transparent 70%),
  var(--light)}
.service{width:189px;height:189px;border-radius:50%;background:var(--white);border:6px solid var(--ring);top:476px;text-align:center}
.service.active{background:var(--red)}
.service svg{position:absolute;left:44px;top:22px;width:90px;height:90px;fill:none;stroke:var(--ink);stroke-width:3;stroke-linecap:round;stroke-linejoin:round}
.service.active svg{stroke:var(--white)}
.service span{position:absolute;left:0;right:0;top:122px;font-size:15.5px;font-weight:500;color:var(--ink)}
.service.active span{color:var(--white)}
.welcome-title{left:0;top:742px;width:1200px;text-align:center;font-size:32px;font-weight:500}
.welcome-copy{left:150px;top:823px;width:900px;text-align:center;font-size:12.4px;line-height:25.8px;color:var(--text);white-space:nowrap}
.read-btn{left:511px;top:1005px;width:178px;height:42px;line-height:42px;font-size:12.5px}

/* news */
.news-title{left:0;top:1158px;width:1200px;text-align:center;font-size:32px;font-weight:500}
.card{top:1235px;width:289px;height:239px;overflow:hidden}
.card .photo{position:absolute;inset:0}
.card .badge{position:absolute;left:61px;top:36px;width:167px;height:167px;border-radius:50%;display:flex;flex-direction:column;align-items:center;justify-content:center;color:var(--white);text-align:center;padding:0 12px}
.badge .date{font-size:12px;font-weight:400}
.badge .rule{width:34px;height:2px;background:var(--red);margin:6px 0 8px}
.badge.red .rule{background:var(--white)}
.badge .headline{font-size:12.5px;font-weight:600;line-height:17px}
.badge.red{background:rgba(236,31,39,.92)}
.badge.black{background:rgba(10,10,10,.92)}

/* testimonials */
.testimonials{left:0;top:1527px;width:1200px;height:522px;background:
  radial-gradient(ellipse 260px 200px at 80px 260px,rgba(90,90,90,.35),transparent 70%),
  linear-gradient(180deg,#2b2b2b,#1b1b1b)}
.test-title{left:0;top:1612px;width:1200px;text-align:center;color:var(--white);font-size:32px;font-weight:500}
.portrait{left:146px;top:1689px;width:248px;height:248px;border-radius:50%;border:6px solid var(--red);background:radial-gradient(circle at 50% 40%,#f2f2f2,#d0d0d0 70%,#a8a8a8)}
.quote-mark{left:428px;top:1700px;color:var(--red);font-size:110px;font-weight:700;line-height:1;font-family:Georgia,serif}
.reviewer{left:498px;top:1733px;color:var(--white);font-size:22px;font-weight:500}
.review{left:427px;top:1781px;width:660px;color:#c9c9c9;font-size:15.3px;line-height:25.8px;font-weight:300}
.dot{left:1146px;width:10px;height:10px;border-radius:50%;background:#cfcfcf}
.dot.on{background:var(--red)}

/* footer */
.footer-brand{left:118px;top:2090px;width:130px;text-align:center}
.footer-brand .brand-name{font-size:15px}
.copyright{left:804px;top:2115px;font-size:12px;color:var(--ink)}
.page-code{left:1140px;top:2115px;font-size:12px;color:var(--ink)}
</style>
</head>
<body>

<div class="abs hero" role="img" aria-label="Industrial plant and harbour at dusk with smokestacks and storage tanks"></div>
<div class="abs hero-shade"></div>

<nav class="abs nav">
  <a class="active" href="#" style="left:108px">Home</a>
  <a href="#" style="left:247px">About Us</a>
  <a href="#" style="left:372px">Services</a>
  <a href="#" style="left:743px">FAQs</a>
  <a href="#" style="left:833px">Clients</a>
  <a href="#" style="left:944px">Contact Us</a>
</nav>
<div class="abs brand-badge"><div class="brand-name">Brackenford<br>Fluidworks</div></div>

<h1 class="abs hero-title">Brackenford Fluidworks</h1>
<p class="abs hero-sub">Brackenford Fluidworks is a full hydraulic repair facility</p>
<a class="abs btn hero-btn" href="#">Learn More</a>

<section class="abs welcome" role="img" aria-label="Faint photo of a heavy equipment trailer"></section>

<div class="abs service active" style="left:154px">
  <svg viewBox="0 0 90 90" aria-hidden="true"><rect x="14" y="14" width="62" height="10" rx="2"/><line x1="22" y1="24" x2="22" y2="32"/><line x1="68" y1="24" x2="68" y2="32"/><rect x="34" y="24" width="22" height="30" rx="3"/><line x1="38" y1="34" x2="52" y2="34"/><line x1="38" y1="42" x2="52" y2="42"/><line x1="45" y1="54" x2="45" y2="80"/><line x1="40" y1="80" x2="50" y2="80"/></svg>
  <span>Pumps</span></div>
<div class="abs service" style="left:391px">
  <svg viewBox="0 0 90 90" aria-hidden="true"><circle cx="52" cy="28" r="17"/><line x1="52" y1="28" x2="60" y2="20"/><line x1="52" y1="45" x2="52" y2="58"/><rect x="30" y="58" width="46" height="16" rx="4"/><line x1="10" y1="66" x2="30" y2="66"/><line x1="76" y1="66" x2="84" y2="66"/><path d="M22 66 V38 a8 8 0 0 1 16 0 v10"/></svg>
  <span>Valves</span></div>
<div class="abs service" style="left:624px">
  <svg viewBox="0 0 90 90" aria-hidden="true"><rect x="14" y="24" width="62" height="46" rx="5"/><rect x="26" y="12" width="38" height="12" rx="2"/><line x1="8" y1="38" x2="14" y2="38"/><line x1="8" y1="56" x2="14" y2="56"/><line x1="76" y1="38" x2="84" y2="38"/><line x1="76" y1="56" x2="84" y2="56"/><circle cx="56" cy="47" r="9"/><circle cx="56" cy="47" r="3"/><line x1="22" y1="47" x2="44" y2="47"/><line x1="22" y1="78" x2="68" y2="78"/></svg>
  <span>Motors</span></div>
<div class="abs service" style="left:854px">
  <svg viewBox="0 0 90 90" aria-hidden="true"><rect x="40" y="6" width="10" height="8" rx="2"/><path d="M32 24 a13 10 0 0 1 26 0 V80 H32 Z"/><line x1="32" y1="64" x2="58" y2="64"/><line x1="45" y1="34" x2="45" y2="44"/><circle cx="45" cy="50" r="1.2"/></svg>
  <span>Cylinders</span></div>

<h2 class="abs welcome-title">Welcome to Brackenford Fluidworks</h2>
<p class="abs welcome-copy">Brackenford Fluidworks is a full hydraulic repair facility. We have 2 shops. We repair and service all hydraulic cylinders, pneumatic cylinders,<br>hydraulic pumps, motors, valves and gearboxes. Our services range from large industrial plants to the individual that owns one piece of<br>equipment. We also offer removal and install of cylinders. Along with free pick up and delivery, within a certain distance which is usually<br>100 miles from one of our shops. With over 30 years experience in the hydraulic business, we can repair or replace any job.<br>There is not a job too big or too small, we service them all.</p>
<a class="abs btn read-btn" href="#">Read More</a>

<h2 class="abs news-title">Recent News</h2>

<article class="abs card" style="left:144px">
  <div class="photo" role="img" aria-label="Repaired hydraulic part on a wooden pallet" style="background:radial-gradient(ellipse 140px 60px at 140px 200px,rgba(230,225,215,.7),transparent 70%),linear-gradient(160deg,#3a3026,#7a5a3a 40%,#a07a4e 60%,#5a4330)"></div>
  <div class="badge red"><div class="date">March 3rd 2018</div><div class="rule"></div><div class="headline">At vero eos et<br>accusamus et iusto<br>odio dignissimos<br>ducimus qui</div></div>
</article>
<article class="abs card" style="left:456px">
  <div class="photo" role="img" aria-label="Hydraulic components laid out on a shop floor" style="background:radial-gradient(ellipse 120px 70px at 180px 200px,rgba(220,220,220,.6),transparent 70%),linear-gradient(150deg,#2a2a2a,#6e6e6e 45%,#9a9a9a 60%,#3a3a3a)"></div>
  <div class="badge black"><div class="date">March 3rd 2018</div><div class="rule"></div><div class="headline">At vero eos et<br>accusamus et iusto<br>odio dignissimos<br>ducimus qui</div></div>
</article>
<article class="abs card" style="left:766px">
  <div class="photo" role="img" aria-label="Stacked hydraulic cylinders ready for delivery" style="background:radial-gradient(ellipse 150px 50px at 150px 140px,rgba(200,200,200,.55),transparent 70%),linear-gradient(180deg,#1e1e1e,#5a5a5a 40%,#8a8a8a 60%,#2a2a2a)"></div>
  <div class="badge black"><div class="date">March 3rd 2018</div><div class="rule"></div><div class="headline">At vero eos et<br>accusamus et iusto<br>odio dignissimos<br>ducimus qui</div></div>
</article>

<section class="abs testimonials" role="img" aria-label="Dark photo of hydraulic cylinders in a workshop"></section>
<h2 class="abs test-title">Testimonials</h2>
<div class="abs portrait" role="img" aria-label="Portrait of the customer giving the testimonial"></div>
<div class="abs quote-mark">&ldquo;</div>
<div class="abs reviewer">Daniel Okafor</div>
<p class="abs review">At vero eos et accusamus et iusto odio dignissimos ducimus qui blanditiis praesentium voluptatum deleniti atque corrupti quos dolores et quas molestias excepturi sint occaecati cupiditate non provident, similique sunt in culpa qui officia deserunt mollitia animi, id est laborum et dolorum fuga. Et harum quidem rerum facilis est et expedita distinctio.</p>
<div class="abs dot on" style="top:1790px"></div>
<div class="abs dot" style="top:1815px"></div>
<div class="abs dot" style="top:1841px"></div>
<div class="abs dot" style="top:1867px"></div>

<footer>
  <div class="abs footer-brand"><div class="brand-name">Brackenford<br>Fluidworks</div></div>
  <div class="abs copyright">© 2018 Company Name | &nbsp;All Rights Reserved</div>
  <div class="abs page-code">C5</div>
</footer>

</body>
</html>
```